BUSINESS CARD - HALLORAN FIELD SERVICES

I would like to create a business card for my fertilizer spreading business. I would like to incorporate my existing logo and also a description of the services offered. The business card will be given to farmers so must be kept simple but effective. It will also be left in stores so much also be eye catching in order to stand out from other cards.

Target Market(s)

FARMERS

Requirements
Must have
• FRONT OF CARD = EXISTING LOGO + "CUSTOMISED SPREADING" below the logo

REAR Of CARD = SERVICES OFFERED AND CONTACT DETAILS

- Bulk fertilizer including Lime, Gypsum, Manure & Compost
- Granular fertilizer including Single Super, Urea, Gran-am, & Custom Blends
- Modern equipment - Autosteer & Variable Rate Capable
- Friendly & Reliable Service
- Contact Gus: 0417 552 308
Nice to have
• utilize same color scheme as existing logo

```html
<!DOCTYPE html>
<html lang="en">
<head>
<meta charset="utf-8">
<title>Halloran Field Services – Business Card</title>
<link href="https://fonts.googleapis.com/css2?family=Questrial&display=swap" rel="stylesheet">
<style>
  :root {
    --charcoal: #4a4a4c;
    --charcoal-deep: #3c3c3e;
    --stripe-grey: #5b5b5e;
    --orange: #f7941d;
    --white: #ffffff;
    --stage: #e9e7e4;
    --ink: #3f3f41;
  }
  html, body {
    margin: 0;
    padding: 0;
    width: 1200px;
    height: 900px;
    overflow: hidden;
    background: var(--stage);
    font-family: "Questrial", "Century Gothic", sans-serif;
  }
  .canvas {
    position: relative;
    width: 1200px;
    height: 900px;
  }
  .card {
    position: absolute;
    width: 700px;
    height: 400px;
    background: var(--white);
    overflow: hidden;
    box-shadow: 0 10px 28px rgba(0,0,0,0.22);
  }
  .card-back { left: 60px; top: 40px; }
  .card-front { left: 440px; top: 460px; }
  .card svg.art {
    position: absolute;
    inset: 0;
    width: 700px;
    height: 400px;
  }

  /* Back side */
  .contact-line {
    position: absolute;
    left: 34px;
    top: 34px;
    display: flex;
    align-items: center;
    gap: 12px;
    color: var(--ink);
    font-size: 21px;
    letter-spacing: 2px;
  }
  .contact-line svg { width: 30px; height: 24px; }
  .services {
    position: absolute;
    right: 34px;
    top: 172px;
    text-align: right;
    color: var(--white);
  }
  .services-title {
    color: var(--orange);
    font-size: 20px;
    letter-spacing: 1.2px;
    margin: 0 0 10px;
    font-weight: 400;
  }
  .service-list {
    list-style: none;
    margin: 0;
    padding: 0;
    font-size: 16px;
    line-height: 27px;
    letter-spacing: 0.6px;
  }
  .service-list li {
    display: flex;
    justify-content: flex-end;
    align-items: center;
    gap: 8px;
  }
  .bullet {
    width: 13px;
    height: 8px;
    flex: none;
  }

  /* Front side */
  .brand {
    position: absolute;
    right: 40px;
    top: 62px;
    display: flex;
    align-items: center;
    gap: 14px;
  }
  .brand-dot {
    width: 44px;
    height: 44px;
    border-radius: 50%;
    background: var(--charcoal);
  }
  .brand-name {
    color: var(--charcoal);
    font-size: 27px;
    letter-spacing: 1.5px;
  }
  .tagline {
    position: absolute;
    left: 58px;
    bottom: 36px;
    color: var(--orange);
    font-size: 46px;
    letter-spacing: 3px;
    margin: 0;
    font-weight: 400;
  }
</style>
</head>
<body>
<main class="canvas">

  <!-- Rear of card -->
  <section class="card card-back" aria-label="Card rear: services and contact">
    <svg class="art" viewBox="0 0 700 400" aria-hidden="true">
      <path d="M0 143 C 180 158, 380 58, 700 8" fill="none" stroke="var(--stripe-grey)" stroke-width="7"/>
      <path d="M0 160 C 180 175, 380 75, 700 25" fill="none" stroke="var(--orange)" stroke-width="9"/>
      <path d="M0 175 C 180 190, 380 90, 700 40 L700 400 L0 400 Z" fill="var(--charcoal)"/>
    </svg>
    <svg class="art" viewBox="0 0 700 400">
      <ellipse role="img" aria-label="Wheat ear ornament along the curve" cx="610" cy="26" rx="70" ry="18" transform="rotate(-8 610 26)" fill="var(--charcoal-deep)"/>
    </svg>

    <div class="contact-line">
      <svg viewBox="0 0 30 24" aria-hidden="true">
        <path d="M2 9 C 2 3, 28 3, 28 9 L 22 10 L 21 7 L 9 7 L 8 10 Z" fill="var(--orange)"/>
        <path d="M7 11 L23 11 L26 22 L4 22 Z" fill="var(--orange)"/>
        <circle cx="15" cy="16" r="3" fill="var(--white)"/>
      </svg>
      <span class="phone">0417 552 308</span>
    </div>

    <div class="services">
      <h2 class="services-title">Services Offered And Contact Details</h2>
      <ul class="service-list">
        <li>Bulk fertilizer including Lime, Gypsum, Manure &amp; Compost<svg class="bullet" viewBox="0 0 13 8" aria-hidden="true"><path d="M0 0 L6.5 8 L13 0 L6.5 3 Z" fill="var(--orange)"/></svg></li>
        <li>Granular fertilizer including Single Super<svg class="bullet" viewBox="0 0 13 8" aria-hidden="true"><path d="M0 0 L6.5 8 L13 0 L6.5 3 Z" fill="var(--orange)"/></svg></li>
        <li>Urea, Gran-am, &amp; Custom Blends<svg class="bullet" viewBox="0 0 13 8" aria-hidden="true"><path d="M0 0 L6.5 8 L13 0 L6.5 3 Z" fill="var(--orange)"/></svg></li>
        <li>Modern equipment - Autosteer &amp; Variable Rate Capable<svg class="bullet" viewBox="0 0 13 8" aria-hidden="true"><path d="M0 0 L6.5 8 L13 0 L6.5 3 Z" fill="var(--orange)"/></svg></li>
        <li>Friendly &amp; Reliable Service<svg class="bullet" viewBox="0 0 13 8" aria-hidden="true"><path d="M0 0 L6.5 8 L13 0 L6.5 3 Z" fill="var(--orange)"/></svg></li>
      </ul>
    </div>
  </section>

  <!-- Front of card -->
  <section class="card card-front" aria-label="Card front: brand and tagline">
    <svg class="art" viewBox="0 0 700 400" aria-hidden="true">
      <path d="M200 200 C 380 150, 520 150, 700 128" fill="none" stroke="var(--stripe-grey)" stroke-width="7"/>
      <path d="M200 218 C 380 172, 520 172, 700 150" fill="none" stroke="var(--orange)" stroke-width="9"/>
      <path d="M0 290 C 120 240, 260 226, 400 200 C 520 180, 610 176, 700 166 L700 400 L0 400 Z" fill="var(--charcoal)"/>
    </svg>
    <svg class="art" viewBox="0 0 700 400">
      <ellipse role="img" aria-label="Wheat ear ornament leading into the curve" cx="140" cy="240" rx="118" ry="34" transform="rotate(-14 140 240)" fill="var(--charcoal-deep)"/>
    </svg>

    <div class="brand">
      <span class="brand-dot" aria-hidden="true"></span>
      <span class="brand-name">HALLORAN FIELD SERVICES</span>
    </div>
    <h1 class="tagline">Customised Spreading</h1>
  </section>

</main>
</body>
</html>
```